Steadfast Field Crews

We are a underground coal mining labour hire company, needing a website that links into our online payroll (www.wagelinkr.com.au) and also need to have job applications page that is a preform with drop down menu,s with answers or check boxes. We would also need a 3 tier administration access for access to different files.
We are looking for an ongoing relationship with future app integration

Reason: There are a few more designs to come and I'm out at the mine for another week

Industry/Entity Type

Coal Mining

```html
<!DOCTYPE html>
<html lang="en">
<head>
<meta charset="utf-8">
<title>Steadfast Field Crews – Application Form</title>
<link rel="stylesheet" href="https://fonts.googleapis.com/css2?family=Arimo:wght@400;700&display=swap">
<style>
  :root{
    --black:#000;
    --panel-dark:#1a1a1a;
    --panel-mid:#1c1c1c;
    --rule:#444;
    --text:#a6a6a6;
    --text-soft:#8c8c8c;
    --white:#fff;
    --orange:#f5822a;
    --side-grey:#8a8a8a;
  }
  *{box-sizing:border-box;margin:0;padding:0}
  html,body{width:1200px;height:1042px;overflow:hidden;background:var(--black)}
  body{position:relative;font-family:"Arimo",Arial,sans-serif;color:var(--text)}
  .abs{position:absolute}

  .site-header{left:0;top:0;width:1200px;height:158px;border-bottom:1px solid var(--rule)}
  .brand-mark{left:48px;top:0;width:103px;height:147px;background:#111}
  .brand-name{left:177px;top:60px;font-size:23px;color:var(--white);white-space:nowrap}
  .brand-tagline{left:177px;top:97px;font-size:13px;font-weight:700;letter-spacing:2px;color:#9a9a9a;word-spacing:10px}
  .search{left:925px;top:14px;width:160px;height:22px;border-radius:11px;background:linear-gradient(#777,#5c5c5c)}
  .search svg{position:absolute;right:2px;top:2px}
  .login{left:1124px;top:18px;font-size:16px;color:var(--orange)}

  .main-nav{left:0;top:159px;width:1200px;height:77px;border-bottom:1px solid var(--rule)}
  .main-nav a{position:absolute;top:31px;font-size:17px;color:var(--text-soft);text-decoration:none;white-space:nowrap}

  .stage{left:0;top:237px;width:1200px;height:500px;background:linear-gradient(var(--side-grey),#4a4a4a 45%,var(--black) 90%)}

  .form-panel{left:64px;top:236px;width:1070px;height:661px;background:var(--panel-dark)}
  .form-title-band{left:0;top:0;width:1070px;height:144px;background:var(--black)}
  .form-title{left:8px;top:44px;font-size:36px;font-weight:700;color:var(--orange)}
  .title-art{left:654px;top:0;width:416px;height:144px;background:linear-gradient(110deg,#000 0%,#2b2b2b 30%,#e9742a 55%,#f2f2f2 75%,#222 100%)}

  .row{left:0;width:1070px}
  .row-1{top:144px;height:73px;background:var(--panel-mid)}
  .row-2{top:217px;height:73px;background:var(--black)}
  .row-3{top:290px;height:371px;background:var(--panel-dark)}
  .question{left:32px;font-size:18px;color:var(--text)}
  .row-2 .question{font-weight:700;left:30px}
  .opt{font-size:18px;color:var(--text)}
  .radio{width:15px;height:15px;border:1.5px solid #bbb;border-radius:50%}
  .radio.on::after{content:"";position:absolute;left:3.5px;top:3.5px;width:5px;height:5px;border-radius:50%;background:#ccc}
  .check{width:18px;height:18px;border:1.5px solid #bbb}

  .submit{left:767px;top:897px;width:367px;height:68px;background:var(--orange);color:var(--white);font-size:25px;font-weight:700;text-align:center;line-height:68px;border:none;font-family:inherit}
  .copyright{left:484px;top:1020px;font-size:12px;color:#555}
</style>
</head>
<body>
  <header class="abs site-header">
    <div class="abs brand-mark"></div>
    <div class="abs brand-name">Steadfast Field Crews</div>
    <div class="abs brand-tagline">FLEXIBLE RESOURCEFUL RELIABLE</div>
    <div class="abs search">
      <svg width="18" height="18" viewBox="0 0 18 18"><circle cx="9" cy="9" r="8" fill="#222"/><circle cx="8" cy="8" r="4" fill="none" stroke="#fff" stroke-width="1.5"/><line x1="11" y1="11" x2="14" y2="14" stroke="#fff" stroke-width="1.8"/></svg>
    </div>
    <a class="abs login">LOGIN</a>
  </header>

  <nav class="abs main-nav">
    <a style="left:456px">HOME</a>
    <a style="left:551px">ABOUT</a>
    <a style="left:652px">DOWNLOAD DOCUMENTS</a>
    <a style="left:896px">PAY PORTAL</a>
    <a style="left:1043px">CONTACT US</a>
  </nav>

  <div class="abs stage"></div>

  <form class="abs form-panel">
    <div class="abs form-title-band">
      <h1 class="abs form-title">APPLICATION FORM</h1>
      <div class="abs title-art" role="img" aria-label="Illustration of a miner in a hard hat with an orange burst"></div>
    </div>

    <div class="abs row row-1">
      <p class="abs question" style="top:22px">DO YOU HAVE CURRENT COAL BOARD GENERICS ?</p>
      <span class="abs opt" style="left:777px;top:26px">YES</span>
      <span class="abs radio on" style="left:841px;top:29px"></span>
      <span class="abs opt" style="left:935px;top:26px">NO</span>
      <span class="abs radio" style="left:990px;top:29px"></span>
    </div>

    <div class="abs row row-2">
      <p class="abs question" style="top:23px">DO YOU HAVE A CURRENT&nbsp; COAL BOARD MEDICAL ?</p>
      <span class="abs opt" style="left:778px;top:23px">YES</span>
      <span class="abs radio on" style="left:842px;top:26px"></span>
      <span class="abs opt" style="left:936px;top:23px">NO</span>
      <span class="abs radio" style="left:991px;top:26px"></span>
    </div>

    <div class="abs row row-3">
      <p class="abs question" style="top:25px">WHAT MINE ARE YOU CURRENTLY INDUCTED AT ?</p>
      <span class="abs opt" style="left:774px;top:29px">ASHCOMBE</span>
      <span class="abs check" style="left:987px;top:29px"></span>
      <span class="abs opt" style="left:774px;top:88px">TALLOWRIDGE</span>
      <span class="abs check" style="left:987px;top:86px"></span>
      <span class="abs opt" style="left:773px;top:151px">BRAMBLEDOWN</span>
      <span class="abs check" style="left:987px;top:150px"></span>
      <span class="abs opt" style="left:771px;top:210px">CORRIGAN</span>
      <span class="abs check" style="left:987px;top:208px"></span>
      <span class="abs opt" style="left:772px;top:268px">ETC.</span>
    </div>
  </form>

  <button class="abs submit" type="submit">SUBMIT</button>

  <footer class="abs copyright">Copyright : SFC. 2014</footer>
</body>
</html>
```